WE ARE BRIGHT SPARROW, building a full website with ecommerce

requirements:
CODED FOR SITEQUILL
ONLINE STORE FUNCTION WITH E-COMMERCE USING TRADEBLOOM
PAGEWAVE AND PICTOLANE LINKS

I need a website design for my organization, WE ARE BRIGHT SPARROW, a global empowerment movement elevating woman, and the world. The site's home page should reflect our mission, to empower women. It should have a strong, empowering feel, with minimalistic design.
Please see www.lunavelto.com and http://www.corvenhal.co/ for an inspiration on layout and feel.

**PLEASE SEE ATTACHMENT "LOGO MOCK UP" FOR LOGO. THIS IS NOT THE FINAL VECTOR FILE, BUT THIS LOOKS THE SAME AS THE FINAL LOGO.

HOME PAGE:
The first section of the home page should include a background image with our logo center.

You should include the following links to pages at the top right of the page:
MISSION
MANTRA
ARMOR
MEET BS (I would like "bs" to be our logo)
pagewave and pictolane links

As you scroll down the page, you should see the following sections, which correlate to the links to pages as written above. **SEE ATTACHED SKETCH "HOMEPAGE LAYOUT IDEA" FOR REFERENCE**

WHO WE ARE (correlates to the link Mission)

OUR MANTRA (correlates to the link Mantra)

OUR ARMOR (correlates to the link The Shirt)
(This is where we will sell a shirt (and other apparel) and need the e-commerce function)

MEET BRIGHT SPARROWS (correlates to the link Meet BS)

SHOW OFF YOUR SUPER POWERS (correlates to the pagewave and pictolane)

FEATURED BRIGHT SPARROW (no link on top right of page)

On the homepage, for each of the above sections, as you scroll down there should be an image, either in the background or framed, next to the title (WHO WE ARE, for example), as well as one sentence of small text explaining the title. The title (WHO WE ARE) and the one sentence should link to a page (ie WHO WE ARE + the one sentence links to the MISSION page). ** SEE ATTACHED SKETCH "HOMEPAGE SECTION IDEAS" FOR REFERENCE**

**PLEASE SEE ATTACHMENT "WEBSITE TITLE IDEAS" FOR A STARTING PLACE OF THE LOOK. These don't have to be exact, but they give you an idea of what I'm looking for.

**FONTS TYPOLD EXTRA BOLD AND TYPOLD BOOK 500 (WHICH SHOULD BE BOLDED MANUALLY) ARE ATTACHED**

Target Market(s)

Women, mainly in US

Industry/Entity Type

Social

Coding

Coded - Design and coding required

Number of Pages Required

5+ page

Font styles to use
Other font styles liked:
• Typol Extra Bold

Requirements
Must have
• CODED FOR SITEQUILL
• ONLINE STORE FUNCTION WITH E-COMMERCE USING TRADEBLOOM
• PAGEWAVE AND PICTOLANE LINKS
• Typold Extra Bold and Typold Book 500, attached
• please see description for all requirements
Nice to have
• please see description for all ideas
Should not have

```html
<!DOCTYPE html>
<html lang="en">
<head>
<meta charset="utf-8">
<title>We Are Bright Sparrow</title>
<link href="https://fonts.googleapis.com/css2?family=Montserrat:wght@400;500;600;700;800&display=swap" rel="stylesheet">
<style>
:root{
  --orange:#f26b4e;
  --orange-deep:#e85d42;
  --orange-light:#f7896b;
  --ink:#1b1b1b;
  --white:#ffffff;
  --footer:#141414;
  --muted:#8a8a8a;
}
*{box-sizing:border-box;margin:0;padding:0}
html,body{width:1200px;height:3509px;overflow:hidden}
body{position:relative;font-family:'Montserrat',sans-serif;color:var(--white);background:var(--white)}
a{color:inherit;text-decoration:none}

/* header */
.site-header{position:absolute;top:0;left:0;width:1200px;height:89px;background:var(--white);border-top:4px solid var(--ink)}
.brand{position:absolute;left:164px;top:22px;display:flex;align-items:center;gap:10px;color:var(--ink)}
.brand-square{width:30px;height:30px;border:3px solid var(--ink)}
.brand-name{font-weight:800;font-size:12px;line-height:13px;letter-spacing:.5px}
.main-nav{position:absolute;top:38px;left:561px;color:var(--ink);font-size:13px;font-weight:500;letter-spacing:.5px}
.main-nav a{position:absolute;white-space:nowrap}
.social-nav{position:absolute;top:31px;left:968px;display:flex;gap:10px}
.social-nav a{display:flex;align-items:center;gap:5px;color:var(--ink);font-size:10px;font-weight:700}
.dot{width:16px;height:16px;border-radius:50%;background:var(--orange)}

/* photo stand-ins */
.photo{position:absolute;inset:0}

/* hero */
.hero{position:absolute;top:89px;left:0;width:1200px;height:514px;text-align:center;overflow:hidden}
.hero .photo{background:
  radial-gradient(ellipse 260px 200px at 230px 240px,rgba(214,182,160,.55),transparent 70%),
  radial-gradient(ellipse 240px 220px at 560px 250px,rgba(150,110,95,.55),transparent 70%),
  radial-gradient(ellipse 260px 220px at 880px 230px,rgba(120,85,80,.6),transparent 70%),
  radial-gradient(ellipse 420px 160px at 1050px 90px,rgba(235,232,228,.55),transparent 75%),
  radial-gradient(ellipse 420px 160px at 380px 60px,rgba(225,215,205,.5),transparent 75%),
  linear-gradient(180deg,#a29a94 0%,#6e6560 50%,#3f3835 100%)}
.hero .photo::after{content:"";position:absolute;inset:0;background:rgba(20,18,18,.28)}
.hero-mark{position:absolute;left:574px;top:126px;width:54px;height:54px;border:5px solid var(--white);transform:rotate(45deg)}
.hero-title{position:absolute;top:206px;width:100%;font-size:27px;line-height:38px;letter-spacing:.5px}
.hero-title strong{font-weight:800}
.hero-title span{font-weight:400}
.signup{position:absolute;left:334px;top:301px;width:531px;height:38px;display:flex}
.signup-field{flex:1;background:var(--white);color:var(--muted);font-size:12px;text-align:left;padding:12px 14px}
.signup-btn{width:100px;background:var(--orange);border-radius:0 19px 19px 0;font-size:12px;font-weight:700;padding-top:12px}
.slider-dots{position:absolute;top:458px;left:555px;display:flex;gap:9px}
.slider-dots i{width:14px;height:14px;border-radius:50%;background:var(--white)}
.slider-dots i.active{background:var(--orange)}

/* mission band */
.mission-band{position:absolute;top:603px;left:0;width:1200px;height:178px;background:linear-gradient(90deg,var(--orange-light),var(--orange) 50%,var(--orange-light));text-align:center}
.mission-text{padding-top:20px;font-size:19px;line-height:33px;letter-spacing:.5px;font-weight:400}
.mission-text strong{font-weight:800}
.fly{position:absolute;left:540px;top:102px;display:flex;align-items:center;gap:14px}
.fly-square{width:36px;height:36px;border:4px solid var(--white);transform:rotate(45deg)}
.fly-label{font-weight:800;text-align:left;line-height:1}
.fly-label small{display:block;font-size:17px}
.fly-label b{display:block;font-size:34px}

/* feature sections */
.feature{position:absolute;left:0;width:1200px;height:442px;overflow:hidden}
.feature .photo::after{content:"";position:absolute;inset:0}
.feature-title{position:absolute;display:flex;align-items:center;gap:30px;font-weight:800;font-size:41px;line-height:47px;letter-spacing:.5px}
.feature-title.left{left:174px}
.feature-title.right{right:175px;text-align:right}
.title-square{width:62px;height:62px;border:5px solid var(--white);transform:rotate(45deg);flex:none}
.feature-copy{position:absolute;width:350px;font-size:13px;line-height:22px}
.price{display:block;margin-top:22px;font-weight:700;font-size:17px}
.title-small{display:block;font-size:34px;line-height:40px}

.who{top:781px}
.who .photo{background:
  radial-gradient(ellipse 230px 300px at 600px 220px,rgba(190,160,140,.55),transparent 70%),
  radial-gradient(ellipse 200px 260px at 220px 140px,rgba(140,160,175,.5),transparent 70%),
  radial-gradient(ellipse 300px 180px at 620px 440px,rgba(70,80,95,.7),transparent 70%),
  linear-gradient(90deg,#4a5762 0%,#6f7b84 45%,#5a6670 70%,#46525c 100%)}
.who .photo::after{background:rgba(40,55,70,.35)}

.mantra{top:1223px}
.mantra .photo{background:
  radial-gradient(ellipse 170px 230px at 610px 200px,rgba(190,140,115,.55),transparent 70%),
  radial-gradient(ellipse 150px 200px at 230px 250px,rgba(170,60,50,.55),transparent 70%),
  radial-gradient(ellipse 160px 220px at 980px 180px,rgba(180,120,100,.5),transparent 70%),
  radial-gradient(ellipse 140px 160px at 470px 120px,rgba(160,130,115,.4),transparent 70%),
  linear-gradient(90deg,#3a2420 0%,#543630 45%,#4a302b 70%,#2e1f1e 100%)}
.mantra .photo::after{background:rgba(35,20,18,.3)}

.meet{top:1665px;height:440px}
.meet .photo{background:
  radial-gradient(ellipse 140px 200px at 950px 210px,rgba(255,210,190,.35),transparent 70%),
  radial-gradient(ellipse 700px 120px at 600px 380px,rgba(225,100,75,.55),transparent 75%),
  linear-gradient(180deg,#f47a5d 0%,#f3856a 55%,#ec6e52 100%)}

.armor{top:2105px;height:445px}
.armor .photo{background:
  radial-gradient(ellipse 210px 280px at 680px 200px,rgba(120,100,95,.55),transparent 70%),
  radial-gradient(ellipse 150px 220px at 1070px 230px,rgba(200,190,185,.4),transparent 70%),
  radial-gradient(ellipse 220px 180px at 670px 390px,rgba(25,35,55,.6),transparent 70%),
  linear-gradient(90deg,#353639 0%,#46464a 50%,#5a5a5e 100%)}
.armor .photo::after{background:rgba(30,30,35,.3)}

.powers{top:2550px;height:439px}
.powers .photo{background:
  radial-gradient(ellipse 160px 200px at 650px 180px,rgba(225,180,150,.55),transparent 70%),
  radial-gradient(ellipse 160px 190px at 1020px 250px,rgba(215,150,110,.55),transparent 70%),
  radial-gradient(ellipse 160px 190px at 200px 240px,rgba(200,140,115,.5),transparent 70%),
  radial-gradient(ellipse 160px 160px at 500px 60px,rgba(160,110,90,.5),transparent 70%),
  linear-gradient(90deg,#8a5c48 0%,#a87e68 50%,#8e604c 100%)}
.powers .photo::after{background:rgba(60,35,25,.28)}

.featured{top:2989px;height:445px}
.featured .photo{background:
  radial-gradient(ellipse 200px 260px at 720px 200px,rgba(220,210,200,.35),transparent 70%),
  radial-gradient(ellipse 160px 200px at 300px 200px,rgba(190,170,160,.35),transparent 70%),
  radial-gradient(ellipse 300px 160px at 1000px 100px,rgba(210,205,200,.3),transparent 70%),
  linear-gradient(90deg,#4d4846 0%,#6a6460 50%,#55504d 100%)}
.featured .photo::after{background:rgba(40,38,38,.3)}

.social-square{position:absolute;top:166px;display:flex;flex-direction:column;align-items:center;width:120px;font-size:11px;font-weight:700;letter-spacing:.5px}
.social-square i{width:72px;height:72px;border:5px solid var(--white);transform:rotate(45deg);margin:0 0 22px}

/* footer */
.site-footer{position:absolute;top:3434px;left:0;width:1200px;height:75px;background:var(--footer);font-size:11px;letter-spacing:.5px;display:flex;justify-content:center;align-items:center;gap:18px;color:#d8d8d8}
</style>
</head>
<body>

<header class="site-header">
  <a class="brand" href="#">
    <span class="brand-square"></span>
    <span class="brand-name">WE ARE<br>BRIGHT<br>SPARROW</span>
  </a>
  <nav class="main-nav">
    <a href="#who" style="left:0">MISSION</a>
    <a href="#mantra" style="left:113px">MANTRA</a>
    <a href="#meet" style="left:223px">MEET BS</a>
    <a href="#armor" style="left:326px">ARMOR</a>
  </nav>
  <div class="social-nav">
    <a href="#"><span class="dot"></span>PAGEWAVE</a>
    <a href="#"><span class="dot"></span>PICTOLANE</a>
  </div>
</header>

<section class="hero">
  <div class="photo" role="img" aria-label="Photo of four smiling women sitting together in a bright office"></div>
  <span class="hero-mark"></span>
  <h1 class="hero-title"><strong>WE ARE BRIGHT SPARROW</strong><br><span>AND I WILL CONQUER THE WORLD</span></h1>
  <form class="signup">
    <div class="signup-field">BrightSparrow@postwing.com</div>
    <div class="signup-btn">LET'S FLY</div>
  </form>
  <div class="slider-dots"><i></i><i class="active"></i><i></i><i></i></div>
</section>

<section class="mission-band">
  <p class="mission-text"><strong>WE ARE BRIGHT SPARROW</strong> IS A GLOBAL EMPOWERMENT<br>MOVEMENT ELEVATING WOMEN... AND THE WORLD.</p>
  <a class="fly" href="#"><span class="fly-square"></span><span class="fly-label"><small>LET'S</small><b>FLY</b></span></a>
</section>

<section class="feature who" id="who">
  <div class="photo" role="img" aria-label="Portrait photo of a smiling woman in a blazer, muted blue overlay"></div>
  <a class="feature-title left" href="#" style="top:128px"><span class="title-square"></span><span>WHO<br>WE<br>ARE</span></a>
  <p class="feature-copy" style="left:692px;top:160px">We are a movement of bold women lifting each other up, sharing stories, and turning small acts of courage into change.</p>
</section>

<section class="feature mantra" id="mantra">
  <div class="photo" role="img" aria-label="Photo of a group of smiling women, dark warm overlay"></div>
  <p class="feature-copy" style="left:164px;top:160px">Our words guide every step we take: rise with purpose, speak with heart, and never walk alone on the road ahead.</p>
  <a class="feature-title right" href="#" style="top:151px"><span>OUR<br>MANTRA</span><span class="title-square"></span></a>
</section>

<section class="feature meet" id="meet">
  <div class="photo" role="img" aria-label="Photo of a woman over a city skyline, orange overlay"></div>
  <a class="feature-title left" href="#" style="top:127px"><span class="title-square"></span><span>MEET<br>BRIGHT<br>SPARROWS</span></a>
  <p class="feature-copy" style="left:692px;top:160px">Meet the women leading with grace and grit, building careers, families and communities while lifting the world.</p>
</section>

<section class="feature armor" id="armor">
  <div class="photo" role="img" aria-label="Photo of a smiling woman wearing a dark branded shirt, dark grey overlay"></div>
  <p class="feature-copy" style="left:164px;top:140px">Wear your strength out loud. Every shirt in our armor line is made to remind you of the power you carry.<span class="price">$ 589.00</span></p>
  <a class="feature-title right" href="#" style="top:151px"><span>OUR<br>ARMOR</span><span class="title-square"></span></a>
</section>

<section class="feature powers">
  <div class="photo" role="img" aria-label="Photo of a group of laughing women hugging, warm overlay"></div>
  <a class="feature-title left" href="#" style="top:137px"><span class="title-square"></span><span><span class="title-small">SHOW OFF</span>YOUR SUPER<br>POWERS</span></a>
  <a class="social-square" href="#" style="left:724px"><i></i><span>PAGEWAVE</span></a>
  <a class="social-square" href="#" style="left:836px"><i></i><span>PICTOLANE</span></a>
</section>

<section class="feature featured">
  <div class="photo" role="img" aria-label="Photo of women talking together in a bright room, grey overlay"></div>
  <p class="feature-copy" style="left:164px;top:180px">Each month we shine a light on one woman whose story of courage and kindness inspires us all to fly higher.</p>
  <a class="feature-title right" href="#" style="top:128px"><span>FEATURED<br>BRIGHT<br>SPARROW</span><span class="title-square"></span></a>
</section>

<footer class="site-footer">
  <span>© COPYRIGHT 2017 . ALL RIGHTS RESERVED.</span>
  <a href="#">PRIVACY</a>
  <a href="#">TERMS OF USE</a>
  <a href="#">COOKIES</a>
</footer>

</body>
</html>
```